Pine Ledge Traders, LLC- Global Beverage Company with 100% Cold Chain Logistics

Hey All, My Name is Dale, I am a young business owner in a competitive export space, but my niche is that I am shipping all of my beer around the world, "100% Cold Chain". This model is more costly, but it protects the integrity of the beer itself and will give folks in foreign countries the best representation of what US Craft Beer has to offer.

I am not a branding guy and don't claim to be one, I am a salesperson first, and will be referring to all of you to create something great that will be memorable.

I am looking for a basic Business Card Design for my Craft Beer Export company. I sell US Craft Beer in several countries around the globe. Austrailia, China, Taiwan, Chile, France, New Zealand... to name a few.

I am looking for a sleek, modern, and fresh design. Quickly!

Thanks for your consideration!

Cheers,

Dale

Target Market(s)

International

Contact Information for Business Card

Dale Corrigan
Founder- Roaming Hops Guy
Dale@PineLedgeTraders.example
@RoamingHopsGuy- Instagram only
www.Pineledgetraders.example
@PineLedgeTradersAU- Instagram Only

Font styles to use
Serif

Colors
0592cd
ffffff

Requirements
Must have
• Name-
• Title-
• Email-
• Social Media Handle-
• Company Website-
Nice to have
• Nice Logo/ Images on Card
Should not have
• Tacky Beer Images

```html
<!DOCTYPE html>
<html lang="en">
<head>
<meta charset="utf-8">
<title>Pine Ledge Traders – Business Card</title>
<link rel="stylesheet" href="https://fonts.googleapis.com/css2?family=Marcellus&family=Lato:ital,wght@0,400;1,400&family=Arimo&display=swap">
<style>
  :root {
    --brand-blue: #0592cd;
    --white: #ffffff;
    --steel-grey: #a1a8ad;
    --ink: #3a3a3a;
    --stage: #404040;
  }
  * { margin: 0; padding: 0; box-sizing: border-box; }
  html, body { width: 1200px; height: 900px; overflow: hidden; }
  body { background: var(--stage); position: relative; font-family: "Lato", sans-serif; }

  .card {
    position: absolute;
    top: 306px;
    width: 439px;
    height: 271px;
    overflow: hidden;
    box-shadow: 2px 3px 6px rgba(0,0,0,.45);
  }
  .card--front { left: 149px; background: var(--white); }
  .card--back { left: 609px; background: var(--brand-blue); }

  .name-accent { position: absolute; left: 0; top: 26px; }
  .holder { position: absolute; left: 34px; top: 29px; }
  .holder__name {
    font-family: "Marcellus", serif;
    font-size: 15.5px;
    color: var(--brand-blue);
    letter-spacing: .6px;
    line-height: 1;
  }
  .holder__title { font-size: 11.5px; color: var(--ink); margin-top: 4px; }

  .company {
    position: absolute;
    left: 238px;
    top: 48px;
    width: 182px;
    text-align: center;
  }
  .company__mark {
    width: 22px; height: 22px;
    background: var(--steel-grey);
    margin: 0 auto 10px;
  }
  .company__name {
    font-family: "Marcellus", serif;
    font-size: 20px;
    line-height: 1.05;
    color: var(--brand-blue);
    letter-spacing: .4px;
  }
  .company__tagline {
    font-family: "Arimo", sans-serif;
    font-size: 9.3px;
    letter-spacing: 1.1px;
    color: #6f7478;
    margin-top: 7px;
  }
  .slogan {
    position: absolute;
    right: 22px;
    top: 169px;
    font-family: "Arimo", sans-serif;
    font-style: italic;
    font-size: 11px;
    color: var(--brand-blue);
    letter-spacing: .2px;
  }

  .contact { position: absolute; left: 19px; top: 208px; list-style: none; }
  .contact__item {
    display: flex; align-items: center; gap: 5px;
    font-size: 11.5px; color: var(--ink); line-height: 14px;
  }
  .contact__item svg { flex: none; }
  .social-handle {
    position: absolute; right: 61px; top: 222px;
    font-size: 11.5px; color: var(--ink);
  }
  .footer-bands { position: absolute; left: 0; bottom: 0; }

  .world-map {
    position: absolute; left: 0; top: 0; width: 100%; height: 232px;
    background: linear-gradient(160deg, #1a9dd4 0%, #0592cd 60%, #0a8bc2 100%);
  }
  .markets {
    position: absolute; left: 0; bottom: 0; width: 100%; height: 39px;
    background: var(--steel-grey);
    color: var(--white);
    font-family: "Arimo", sans-serif;
    font-size: 15px;
    display: flex; align-items: center; justify-content: center;
    letter-spacing: .1px;
  }
</style>
</head>
<body>

<section class="card card--front" aria-label="Card front">
  <svg class="name-accent" width="30" height="38" viewBox="0 0 30 38" aria-hidden="true">
    <polygon points="0,0 15,0 15,37 0,37" fill="var(--steel-grey)"/>
    <polygon points="16,0 29,0 29,37 16,37 12,0" fill="var(--brand-blue)"/>
  </svg>
  <div class="holder">
    <div class="holder__name">DALE CORRIGAN</div>
    <div class="holder__title">Founder - Roaming Hops Guy</div>
  </div>

  <div class="company">
    <div class="company__mark"></div>
    <div class="company__name">PINE LEDGE TRADERS</div>
    <div class="company__tagline">GLOBAL BEVERAGE COMPANY</div>
  </div>
  <div class="slogan">100% COLD CHAIN LOGISTICS</div>

  <ul class="contact">
    <li class="contact__item">
      <svg width="9" height="8" viewBox="0 0 9 8" aria-hidden="true">
        <rect width="9" height="8" fill="var(--brand-blue)"/>
        <polyline points="0.5,1 4.5,4.5 8.5,1" fill="none" stroke="#fff" stroke-width="1"/>
      </svg>
      Dale@PineLedgeTraders.example
    </li>
    <li class="contact__item">
      <svg width="9" height="9" viewBox="0 0 9 9" aria-hidden="true">
        <circle cx="4.5" cy="4.5" r="4.5" fill="var(--brand-blue)"/>
        <path d="M2 3 Q4 2 4 4 T6.5 6" fill="none" stroke="#fff" stroke-width="1"/>
      </svg>
      www.Pineledgetraders.example
    </li>
  </ul>
  <div class="social-handle">@RoamingHopsGuy</div>

  <svg class="footer-bands" width="439" height="24" viewBox="0 0 439 24" aria-hidden="true">
    <polygon points="0,12 218,12 213,24 0,24" fill="var(--steel-grey)"/>
    <polygon points="222,2 439,2 439,24 212,24" fill="var(--brand-blue)"/>
  </svg>
</section>

<section class="card card--back" aria-label="Card back">
  <div class="world-map" role="img" aria-label="Dotted world map in white dots on blue"></div>
  <div class="markets">Austrailia | China | Taiwan | Chile | France | New Zealand</div>
</section>

</body>
</html>
```